independent cleaner, reliable, custom, thorough, trustworthy

Not sure yet if I want single-sided or double sided, so I'm selecting double-sided just in case, but single-sided designs are okay.

Really looking to find the happy medium between personal and professional in a business card design. I end up building comfortable relationships with the people I work for.

Most of my business is through referrals, but I want some business cards to hand out to people who ask for one (and maybe put them on community bulletin boards).

My target market is homeowners and business owners who are looking for a reliable cleaner and are willing to pay a bit more to have excellent quality and someone they trust.

Theme: I have a personal-professional feel since I'm solo, so the theme should reflect that. Trustworthy, personal, simple. I clean up messes.

Hopefully this is enough info, let me know if you have any questions though of course!

Target Market(s)

Homeowners businessowners who are looking for a reliable cleaner, excellent quality trustworthy.

Industry/Entity Type

Cleaning Service

Contact Information for Business Card

Please include this text:
• Delphine Marwood
• independent cleaner
• reliable, custom, thorough
• 604-315-2970
• tbh.marwood@quellmail.com

Font styles to use
Serif
Sans Serif

Colors
ffffff
00a990
0492cd
33a6d7
0355a3
3276b5
919191

Requirements
Must have
• Really looking to find the happy medium between personal and professional in a business card design.
• Background: at least 50% white on the side with the most text (coloured accents or shapes are okay)
• I lean more towards simple and clean, solid colours, maybe a gentle gradient
Nice to have
• Not sure yet if I want single-sided or double sided, so I'm selecting double-sided just in case, but single-sided designs are okay.
• Colours: preferably blues and teals for the font and other objects (if any). Open to designer's choice though. I've toyed around with orangey-yellow, but it doesn't feel right and I keep going back to blues/teals
• Also I uploaded a sketch of my signature and initials so you can get a feel for my personality. I'm not expecting this to be included in the design, it's just there.
Should not have
• I don't like a lot of busy-ness or textures
• Also I don't have a logo (not sure where else to specify this)

```html
<!DOCTYPE html>
<html lang="en">
<head>
<meta charset="UTF-8">
<title>Delphine Marwood — Business Card</title>
<link rel="stylesheet" href="https://fonts.googleapis.com/css2?family=Playfair+Display:wght@400;700&display=swap">
<style>
  :root {
    --page-bg: #e6e9ec;
    --card-white: #ffffff;
    --brand-blue: #0c8ccb;
    --brand-blue-light: #1a9bd7;
    --ink: #1c1c1c;
    --ring: #111111;
  }
  * { margin: 0; padding: 0; box-sizing: border-box; }
  html, body {
    width: 1200px;
    height: 900px;
    overflow: hidden;
    background: var(--page-bg);
    font-family: "Playfair Display", Georgia, serif;
  }
  .canvas {
    position: relative;
    width: 1200px;
    height: 900px;
  }
  .card {
    position: absolute;
    left: 320px;
    width: 560px;
    height: 320px;
    border-radius: 20px;
    background: var(--card-white);
    overflow: hidden;
    box-shadow: 0 6px 18px rgba(0,0,0,0.12);
  }
  .card--front { top: 100px; }
  .card--back { top: 480px; }

  /* Front side */
  .front-panel {
    position: absolute;
    left: 0; top: 0;
    width: 210px;
    height: 100%;
    background: linear-gradient(160deg, var(--brand-blue), var(--brand-blue-light));
    display: flex;
    align-items: center;
    justify-content: center;
    padding: 0 22px;
  }
  .front-panel__name {
    color: var(--card-white);
    font-weight: 400;
    font-size: 34px;
    line-height: 1.1;
    text-align: center;
  }
  .front-details {
    position: absolute;
    left: 242px;
    top: 52px;
    color: var(--ink);
  }
  .front-details__name {
    font-weight: 700;
    font-size: 24px;
    margin-bottom: 12px;
  }
  .front-details__line {
    font-weight: 400;
    font-size: 17px;
    line-height: 1.4;
    margin-bottom: 10px;
  }

  /* Back side */
  .back-band {
    position: absolute;
    left: 0;
    top: 96px;
    width: 100%;
    height: 150px;
    background: linear-gradient(90deg, var(--brand-blue), var(--brand-blue-light));
  }
  .back-seal {
    position: absolute;
    left: 135px;
    top: 38px;
    width: 200px;
    height: 200px;
    border-radius: 50%;
    background: var(--card-white);
    border: 3px solid var(--ring);
    display: flex;
    align-items: center;
    justify-content: center;
    text-align: center;
  }
  .back-seal__name {
    color: var(--ink);
    font-weight: 400;
    font-size: 26px;
    line-height: 1.15;
  }
</style>
</head>
<body>
  <main class="canvas">
    <section class="card card--front" aria-label="Business card front">
      <div class="front-panel">
        <span class="front-panel__name">Delphine Marwood</span>
      </div>
      <div class="front-details">
        <p class="front-details__name">Delphine Marwood</p>
        <p class="front-details__line">Independent Cleaner</p>
        <p class="front-details__line">Reliable, Custom, Thorough</p>
        <p class="front-details__line">604-315-2970</p>
        <p class="front-details__line">tbh.marwood@quellmail.com</p>
      </div>
    </section>

    <section class="card card--back" aria-label="Business card back">
      <div class="back-band"></div>
      <div class="back-seal">
        <span class="back-seal__name">Delphine<br>Marwood</span>
      </div>
    </section>
  </main>
</body>
</html>
```